Dynamic Business Card for Sports Supplements Company

Hi! I'm looking for an awesome business card to match my existing sports supplement company. I have uploaded my current company logo and screenshot of the front page of my website.

I would like to have something dynamic and interesting and utilize the colors in the website - the reds and purples

The business card should be double sided and focus on a unique eye-catching design on the back and include all the relevant company info.

Most importantly, it should say somewhere: "Sign up on our website for a coupon code."

Target Market(s)

Mostly for women gym goers but it shouldn't be too feminine. It should be in keeping with the website design. It should flow and clearly be connected to it

Industry/Entity Type

Business

Contact Information for Business Card

Lorraine K. Vestal
CEO
LVestal@Quorvanexco.com
www.quorvanexco.com
555.417.3820
P.O. Box 47315
Harlow Glen, Westmere 00000

Sign up on our website for a coupon code

Font styles to use
Serif
Sans Serif
Other font styles liked:
• Novecento font family and "Quorvanex" is in AR Destine font

Requirements
Must have
• One side should be a bold Quorvanex logo design. Even just the symbol itself may be o.k. (see attached file)

```html
<!DOCTYPE html>
<html lang="en">
<head>
<meta charset="utf-8">
<title>Quorvanex Business Card</title>
<link rel="stylesheet" href="https://fonts.googleapis.com/css2?family=Open+Sans:wght@400;600;700&family=Montserrat:wght@400;500&display=swap">
<style>
  :root {
    --stage: #3a3532;
    --card: #0e0e0e;
    --card-edge: #1c1c1c;
    --red: #ec1c24;
    --white: #ffffff;
    --text-soft: #d9d9d9;
    --divider: #3a1416;
  }
  * { box-sizing: border-box; margin: 0; padding: 0; }
  html, body {
    width: 1200px;
    height: 900px;
    overflow: hidden;
    background: var(--stage);
    font-family: "Open Sans", Arial, sans-serif;
  }
  .canvas {
    position: relative;
    width: 1200px;
    height: 900px;
    display: flex;
    align-items: center;
    justify-content: center;
    gap: 40px;
  }
  .card {
    width: 525px;
    height: 300px;
    background: var(--card);
    border: 1px solid var(--card-edge);
    box-shadow: 0 18px 40px rgba(0,0,0,0.45);
    position: relative;
  }

  /* Contact side */
  .card--contact { display: flex; }
  .brand-panel {
    width: 250px;
    display: flex;
    align-items: center;
    justify-content: center;
    gap: 10px;
  }
  .brand-mark {
    width: 18px;
    height: 18px;
    background: var(--red);
    flex: none;
  }
  .brand-name {
    font-family: "Open Sans", Arial, sans-serif;
    font-weight: 700;
    font-size: 30px;
    color: var(--white);
    letter-spacing: 1px;
  }
  .divider {
    width: 1px;
    margin: 60px 0;
    background: var(--divider);
  }
  .contact-panel {
    padding: 68px 0 0 22px;
    color: var(--text-soft);
    font-size: 13px;
    line-height: 1.35;
  }
  .person-name {
    color: var(--red);
    font-size: 17px;
    font-weight: 400;
    text-transform: uppercase;
    letter-spacing: 0.3px;
  }
  .person-title { font-size: 12px; margin-bottom: 10px; }
  .contact-list { list-style: none; margin-bottom: 12px; }
  .contact-list li { display: flex; align-items: center; gap: 8px; }
  .contact-list svg { width: 9px; height: 9px; flex: none; }
  .icon-fill { fill: var(--red); }
  .icon-cut { fill: none; stroke: var(--card); stroke-width: 1; }
  .address { font-style: normal; }

  /* Brand side */
  .card--brand {
    display: flex;
    flex-direction: column;
    align-items: center;
    justify-content: center;
  }
  .wordmark { display: flex; align-items: center; gap: 12px; }
  .wordmark .brand-name { font-size: 40px; }
  .wordmark .brand-mark { width: 22px; height: 22px; }
  .tagline {
    font-family: "Montserrat", Arial, sans-serif;
    font-size: 13px;
    letter-spacing: 2.6px;
    color: var(--text-soft);
    text-transform: uppercase;
    margin-top: 4px;
  }
  .offer {
    margin-top: 14px;
    font-size: 12px;
    font-weight: 600;
    color: var(--red);
  }
</style>
</head>
<body>
<main class="canvas">
  <section class="card card--contact" aria-label="Contact side">
    <div class="brand-panel">
      <span class="brand-mark"></span>
      <span class="brand-name">Quorvanex</span>
    </div>
    <div class="divider"></div>
    <div class="contact-panel">
      <h1 class="person-name">Lorraine K. Vestal</h1>
      <p class="person-title">CEO</p>
      <ul class="contact-list">
        <li><svg viewBox="0 0 10 10" aria-hidden="true"><path class="icon-fill" d="M2 0.5l2 2-1 1.2a6 6 0 0 0 3.3 3.3l1.2-1 2 2-1.3 1.5C4.5 9.5 0.5 5.5 0.5 1.8z"/></svg>555.417.3820</li>
        <li><svg viewBox="0 0 10 10" aria-hidden="true"><rect class="icon-fill" x="0" y="2" width="10" height="6.5"/><path class="icon-cut" d="M0.5 2.5L5 5.8L9.5 2.5"/></svg>LVestal@Quorvanexco.com</li>
        <li><svg viewBox="0 0 10 10" aria-hidden="true"><circle class="icon-fill" cx="5" cy="5" r="4.6"/></svg>www.quorvanexco.com</li>
      </ul>
      <address class="address">P.O. Box 47315<br>Harlow Glen, Westmere 00000</address>
    </div>
  </section>

  <section class="card card--brand" aria-label="Brand side">
    <div class="wordmark">
      <span class="brand-mark"></span>
      <span class="brand-name">Quorvanex</span>
    </div>
    <p class="tagline">Your Performance Partner</p>
    <p class="offer">Sign up on our website for a coupon code</p>
  </section>
</main>
</body>
</html>
```